Small Business Directory Site Requires a Professional Responsive Web Design

Small Business Directory and Coupon Site - we require a complete website design for a brand new responsive & mobile friendly website. We already have a coder who will professional code our website in Magento.

All PSD pages need to be professionally designed then uploaded into a sharedrive (i.e. like filecrate). Additionally, as I cannot pre-empt everything, please note that we may require a little more assistance once the files have been transferred (for example, in www.brightlane-listings.example if you hover your mouse on the search box you will see a pop up box. We want one of these too and I think that means there may be extra design work here)

We have some draft page sketches have been created (there are some minor changes we want to the sketches provided though); however, we require an excellent designer to add the creative touches to it to make it look professionally created. All artwork/font must be legal.

-------------------------
We like the look of the www.brightlane-listings.example and www. marlowfolio.example

For the headers, please consider a font similar to RNS camellia. We likes this style, but it is too thin for the headers...so we need a variation like this one. For the copy/general text font, something basic that marries well with the headers.

---------------------

Please be sure to also read the brief we wrote for the coder as this will help with better understanding our design requirements.

In total I believe we have about 50 pages. This includes all the little pages and most of the pop up boxes (but not the little help key boxes). For example, pages include...

1. Login (this is where customers log in and can edit, manage their profiles. This means that there are backend membership pages)
2. Mini Services (same look and feel as the business coupons)
3. Resource Centre
4. Join (this is where customers learn about the packages available to submit a directory listing, if they ‘buy’ a package (i.e. free, $25 or $150 package) then they can create their own directory listing)
5. Search the directory (customer can view all the categories and also search the directory)
6. Create a directory listing (this is where customers learn about the packages available to submit a directory listing, if they ‘buy’ a package (i.e. free, $25 or $150 package) then they can create their own directory listing)
7. Quote finder (also know as Get a Quote)
8. Coupons (customer go to the business coupon page and can view all current coupons/submit a coupon)
9. Submit a coupon (form)
10.Advertise with us (form)
11. Join the forum
12.Submit an article or video (form)
13. Affiliates (listing of affiliates we currently have)
14. Become an affiliate (form)
15. Case studies (customer can view the case studies we have in the resource centre)
16. Help Guides (customer can view the help guides we have in the resource centre)
17. About Us
18 .Contact Us (form)
19. Terms & Condition
20. Privacy Policy
21. Supporting City Councils
22. Site Map
23. Forgot password / login details
24. Homepage
25. If we hover over a few areas (i.e. search box, location field) it pops up with more information.
etc etc etc. . . there are more pages.

Please see our filecrate link for the draft mock up pages that I have created so far.

https://www.cloudtrunk.example/sh/qk72pmw4rtz8nd/KLMvbTq2fWndxPzs8Yh4ecRQu

We are in a rush! We'd like to get the majority of the artwork completed by the end of the month. Minor fixes/tweaks can occur thereafter.

Target Market(s)

Small Businesses (employees 0 - 50) located throughout Australia

Industry/Entity Type

Business

Font styles to use
Sans Serif

Requirements
Must have
• Professional. Artwork must be legal (cannot be cut and paste or taken off other websites, must be legally purchased and used).Must look contemporary, fresh, modern.

Absolutely must be a responsive site!
Nice to have
• original work, original photos, original art.

like modern, fresh photos that demonstrate innovation, growth, small business, Australian scenery, stability, goals/passion.
Should not have
• cut and paste graphics, illegal graphics, not purchased graphics.

```html
<!DOCTYPE html>
<html lang="en">
<head>
<meta charset="utf-8">
<title>Wattle Business Link — Home</title>
<link href="https://fonts.googleapis.com/css2?family=Source+Sans+3:wght@600;700&family=Arimo:wght@400;700&display=swap" rel="stylesheet">
<style>
:root{
  --black:#000;
  --band:#111;
  --copy-band:#1b1b1b;
  --orange:#e07b2a;
  --white:#fff;
  --grey-text:#777;
  --dark-text:#333;
  --foot-text:#9a9a9a;
  --head-font:"Source Sans 3",sans-serif;
  --body-font:"Arimo",sans-serif;
}
*{margin:0;padding:0;box-sizing:border-box}
html,body{width:986px;height:1200px;overflow:hidden;background:var(--white);font-family:var(--body-font)}
.page{position:relative;width:986px;height:1200px}

/* header */
.site-header{position:absolute;left:0;top:0;width:986px;height:101px;background:var(--black)}
.brand{position:absolute;left:110px;top:36px;display:flex;align-items:center;gap:8px;color:var(--white);font-family:var(--head-font);font-weight:600;font-size:19px}
.brand-mark{width:14px;height:14px;background:var(--orange);border-radius:50%}
.field{position:absolute;top:34px;height:35px;border:1px solid var(--white);color:var(--white);font-size:9px;padding:13px 12px 0}
.field-what{left:358px;width:148px}
.field-where{left:561px;width:148px}
.near{position:absolute;left:521px;top:44px;color:#ddd;font-size:13px}
.search-btn{position:absolute;left:715px;top:34px;width:39px;height:35px;background:var(--orange)}
.nav-link{position:absolute;top:47px;color:var(--white);font-size:11px;font-weight:700}

/* hero */
.hero{position:absolute;left:0;top:101px;width:986px;height:418px;
  background:linear-gradient(180deg,#6a3f12 0%,#b8661b 28%,#e49a3a 40%,#8a4a14 55%,#3a2510 70%,#6b5132 85%,#4a3a26 100%)}
.hero-title{position:absolute;left:115px;top:146px;color:var(--white);font-family:var(--head-font);font-weight:700;font-size:33px;letter-spacing:.3px}
.hero-sub{position:absolute;left:115px;top:190px;color:var(--white);font-family:var(--head-font);font-weight:700;font-size:24px}
.hero-btn{position:absolute;left:116px;top:238px;width:200px;height:40px;background:var(--orange);color:var(--white);font-family:var(--head-font);font-weight:600;font-size:14px;display:flex;align-items:center;justify-content:center}
.directory{position:absolute;left:629px;top:72px;width:233px;height:273px;background:rgba(150,150,150,.7);border:8px solid rgba(170,170,170,.6);text-align:center;color:var(--white)}
.directory h2{font-family:var(--head-font);font-weight:700;font-size:24px;margin-top:14px}
.directory p{font-size:10px;line-height:21px;margin:12px 8px 0}
.directory-btn{display:inline-block;margin-top:14px;background:#222;color:var(--white);font-family:var(--head-font);font-weight:600;font-size:11.5px;padding:11px 13px}
.arrows{position:absolute;left:0;right:0;bottom:14px;display:flex;justify-content:center;gap:9px}
.pager{position:absolute;left:457px;top:386px;display:flex;gap:4px}
.pager span{width:11px;height:11px;border:2px solid var(--white);border-radius:50%}
.pager .on{background:var(--orange)}

/* community */
.section-title{position:absolute;left:0;width:986px;top:546px;text-align:center;color:var(--orange);font-family:var(--head-font);font-weight:700;font-size:19.5px}
.card{position:absolute;top:594px;width:249px;text-align:center}
.card-media{width:249px;height:158px}
.card-logo{width:249px;height:158px;border:1px solid #ddd;display:flex;align-items:center;justify-content:center;gap:8px;font-family:var(--head-font);font-weight:700;font-size:24px;color:#1b3a6b}
.card-logo i{width:20px;height:20px;background:#1b8fd0}
.card h3{margin-top:13px;font-family:var(--head-font);font-weight:700;font-size:12px;color:var(--dark-text)}
.card p{margin-top:12px;font-size:9.2px;line-height:18.5px;color:var(--grey-text)}

/* partners */
.partners{position:absolute;left:0;top:875px;width:986px;height:81px;background:var(--band);display:flex;align-items:center;justify-content:space-around;padding:0 110px}
.partner{color:var(--white);font-family:var(--head-font);font-weight:700;font-size:30px}

/* footer */
.site-footer{position:absolute;left:0;top:956px;width:986px;height:194px;background:var(--black)}
.foot-col{position:absolute;top:22px}
.foot-col h4{color:var(--white);font-family:var(--head-font);font-weight:700;font-size:12px;margin-bottom:14px}
.foot-col li{list-style:none;color:var(--foot-text);font-size:9.5px;line-height:20px;padding-left:16px;position:relative}
.foot-col li::before{content:"";position:absolute;left:5px;top:8px;width:4px;height:4px;border-radius:50%;background:var(--foot-text)}
.social{display:flex;gap:7px;margin-top:14px}
.social span{width:27px;height:27px;border:1.5px solid var(--white);border-radius:50%}
.copyright{position:absolute;left:0;top:1150px;width:986px;height:50px;background:var(--copy-band);color:#bbb;font-size:9.5px;text-align:center;line-height:50px}
</style>
</head>
<body>
<div class="page">
  <header class="site-header">
    <div class="brand"><span class="brand-mark"></span>Wattle Business Link</div>
    <div class="field field-what">What Do You Want To Find?</div>
    <span class="near">Near</span>
    <div class="field field-where">Chennai,25</div>
    <div class="search-btn">
      <svg width="39" height="35" viewBox="0 0 39 35"><circle cx="18" cy="16" r="4.5" fill="none" stroke="#fff" stroke-width="2"/><line x1="21" y1="19" x2="24" y2="22" stroke="#fff" stroke-width="2.5"/></svg>
    </div>
    <span class="nav-link" style="left:787px">LOGIN</span>
    <span class="nav-link" style="left:851px">JOIN</span>
  </header>

  <section class="hero" role="img" aria-label="Sunset over open Australian plains with birds in flight">
    <h1 class="hero-title">LET US HELP YOU GROW</h1>
    <p class="hero-sub">AUSTRALIA’S SMALL BUSINESS SUPPORT LINK</p>
    <div class="hero-btn">JOIN WATTLE BUSINESS LINK</div>
    <div class="directory">
      <h2>DIRECTORY</h2>
      <p>Our small business directory is maintained to give members choice. We’re open toall businesses, regardless of your location,so long as they service Australian small businesses.</p>
      <span class="directory-btn">CREATE YOUR FREE LISTING</span>
      <div class="arrows">
        <svg width="15" height="15"><circle cx="7.5" cy="7.5" r="7.5" fill="#333"/><path d="M9 4 L5.5 7.5 L9 11" fill="none" stroke="#fff" stroke-width="1.6"/></svg>
        <svg width="15" height="15"><circle cx="7.5" cy="7.5" r="7.5" fill="#333"/><path d="M6 4 L9.5 7.5 L6 11" fill="none" stroke="#fff" stroke-width="1.6"/></svg>
      </div>
    </div>
    <div class="pager"><span></span><span></span><span class="on"></span><span></span><span></span></div>
  </section>

  <h2 class="section-title">GET REAL SUPPORT FROM OUR COMMUNITY</h2>

  <article class="card" style="left:108px">
    <div class="card-media" role="img" aria-label="Business people shaking hands in an office" style="background:linear-gradient(135deg,#c9d8ea,#8fa9c8 60%,#5f7fa6)"></div>
    <h3>HOW DID YOU SORT YOUR BUSINESS?</h3>
    <p>Learn from Dana Prewitt, a real small business owner. How she started her business and what are the most valuable resourcesfor her right now</p>
  </article>
  <article class="card" style="left:369px">
    <div class="card-media" role="img" aria-label="Support team with headsets working at laptops" style="background:linear-gradient(135deg,#e6e6e6,#9aa0a8 55%,#3b3f47)"></div>
    <h3>WHY GO WITH WATTLE BUSINESS LINK?</h3>
    <p>What small business owner can't relate to the ongoing task of attracting new customers? Struggling with cash flow? Or how about not having enough time in the day</p>
  </article>
  <article class="card" style="left:628px">
    <div class="card-logo"><i></i>Keystone Cover</div>
    <h3>BECOME AN AFFILIATE</h3>
    <p>If you have a network of small businesses, let us help to create additional value for your members and make money Talk to us today about how we can help.</p>
  </article>

  <section class="partners">
    <span class="partner">Granford</span>
    <span class="partner">Panelworks</span>
    <span class="partner">Norvale</span>
    <span class="partner">Granford</span>
  </section>

  <footer class="site-footer">
    <div class="foot-col" style="left:108px"><h4>SITE DIRECTORY</h4><ul><li>News &amp; Articles</li><li>Find a Business</li><li>Maps &amp; Directions</li><li>White Pages</li><li>Mobile Apps</li><li>Reverse Phone Lookup</li></ul></div>
    <div class="foot-col" style="left:265px"><h4>RESOURCES</h4><ul><li>Join the Forum</li><li>Submit an Article</li><li>Affiliates</li><li>Become an Affiliate</li><li>Case Studies</li><li>Help Guides</li></ul></div>
    <div class="foot-col" style="left:409px"><h4>POPULAR CATEGORES</h4><ul><li>News &amp; Articles</li><li>Find a Business</li><li>Maps &amp; Directions</li><li>White Pages</li><li>Mobile Apps</li><li>Reverse Phone Lookup</li></ul></div>
    <div class="foot-col" style="left:576px"><h4>ABOUT US</h4><ul><li>About Us</li><li>Contact Us</li><li>Terms &amp; Condition</li><li>Privacy Polacy</li><li>Supporting City</li><li>Site Map</li></ul></div>
    <div class="foot-col" style="left:716px"><h4>FOLLOW US</h4><div class="social"><span></span><span></span><span></span><span></span><span></span></div></div>
  </footer>
  <div class="copyright">© Copy Rights 2014.Wattle Business Link.All Rights Reserved.</div>
</div>
</body>
</html>
```